Dietitian needs awesome business card

I need a contemporary design that's eye catching but professional.
My card is to given to doctors, specialists and patients alike.
I manage patients with chronic diseases
I have uploaded my logo and current business card, I would also like the other Certified Clinical Nutritionist logo incorporated into the design

Target Market(s)

Doctors, specialists and patients

Industry/Entity Type

Healthcare

Contact Information for Business Card

www.brightfieldnutrition.com.au
Ph: 0427 561 903
Fax: 6457 2183
email: marcus.k.diet@fernmail.com
Space on the back of the card with: Appointment date, Appointment time and appointment location

Font styles to use
Serif

Colors
fbee3e
876aae
ffc214

Requirements
Must have
• My Logo
• Certified Clinical Nutritionist Logo
• My 4 locations - Pinebrook Medical Centre, North Corrin Health, Hollis Medical, Ashcombe Doctors Surgery
Nice to have
• I like the colours in my current business card

```html
<!DOCTYPE html>
<html lang="en">
<head>
<meta charset="utf-8">
<title>Brightfield Nutrition & Dietetics – Business Card</title>
<link href="https://fonts.googleapis.com/css2?family=Montserrat:wght@400;500;600;800&display=swap" rel="stylesheet">
<style>
  :root {
    --bg: #e4e4e6;
    --card: #ffffff;
    --blue: #1f6fc1;
    --green: #4aa53a;
    --lime: #8cc63f;
    --grey: #8a8a8a;
    --line: #c9c9c9;
    --orange: #f47a20;
  }
  * { margin: 0; padding: 0; box-sizing: border-box; }
  html, body { width: 1200px; height: 1200px; overflow: hidden; }
  body {
    background: var(--bg);
    font-family: "Montserrat", sans-serif;
    position: relative;
  }
  .card {
    position: absolute;
    left: 150px;
    width: 900px;
    height: 500px;
    background: var(--card);
    border-radius: 40px;
    box-shadow: 0 6px 18px rgba(0,0,0,0.12);
  }
  .card--front { top: 70px; }
  .card--back { top: 630px; }

  /* Brand lockup */
  .brand { position: absolute; display: flex; align-items: center; }
  .brand__dot { border-radius: 50%; background: var(--lime); flex: none; }
  .brand__name { color: var(--blue); font-weight: 600; line-height: 1.05; }
  .brand__name span { display: block; }

  .card--front .brand { left: 150px; top: 150px; gap: 30px; }
  .card--front .brand__dot { width: 110px; height: 110px; }
  .card--front .brand__name { font-size: 64px; }
  .card--front .brand__name span:last-child { font-size: 30px; margin-top: 6px; }

  .appointment { position: absolute; left: 60px; right: 60px; bottom: 60px; }
  .appointment__label { font-size: 13px; color: var(--grey); letter-spacing: 1px; margin-bottom: 40px; }
  .appointment__line { border-top: 1.5px solid var(--line); }

  /* Back */
  .card--back .brand { left: 50px; top: 70px; gap: 14px; }
  .card--back .brand__dot { width: 60px; height: 60px; }
  .card--back .brand__name { font-size: 34px; }
  .card--back .brand__name span:last-child { font-size: 16px; margin-top: 2px; }

  .person { position: absolute; left: 60px; top: 190px; }
  .person__name { font-size: 38px; font-weight: 800; color: var(--blue); }
  .person__role { font-size: 14px; color: var(--grey); letter-spacing: 1.5px; margin-top: 6px; }

  .divider { position: absolute; left: 500px; top: 170px; width: 3px; height: 80px; background: var(--green); }

  .contact { position: absolute; left: 530px; top: 160px; list-style: none; }
  .contact li { display: flex; align-items: center; gap: 10px; font-size: 14px; color: var(--grey); letter-spacing: 1px; margin-bottom: 6px; }
  .contact svg { width: 14px; height: 14px; flex: none; }

  .badge { position: absolute; right: 50px; top: 40px; width: 120px; height: 54px; background: var(--orange); border-radius: 4px; }

  .locations { position: absolute; left: 50px; right: 40px; bottom: 55px; display: flex; justify-content: space-between; }
  .location { border-left: 4px solid var(--green); padding-left: 10px; font-size: 12.5px; color: var(--grey); line-height: 1.45; letter-spacing: 0.5px; }
  .location__name { color: var(--blue); font-weight: 600; font-size: 13.5px; }
</style>
</head>
<body>

<section class="card card--front">
  <div class="brand">
    <div class="brand__dot"></div>
    <div class="brand__name"><span>Brightfield</span><span>Nutrition &amp; Dietetics</span></div>
  </div>
  <div class="appointment">
    <p class="appointment__label">Appointment date/time/location:</p>
    <div class="appointment__line"></div>
  </div>
</section>

<section class="card card--back">
  <div class="brand">
    <div class="brand__dot"></div>
    <div class="brand__name"><span>Brightfield</span><span>Nutrition &amp; Dietetics</span></div>
  </div>

  <div class="badge" role="img" aria-label="Certified Clinical Nutritionist badge"></div>

  <div class="person">
    <h1 class="person__name">Marcus Kellaway</h1>
    <p class="person__role">Practising Dietitian, Nutritionist, and Chef</p>
  </div>

  <div class="divider"></div>

  <ul class="contact">
    <li><svg viewBox="0 0 14 14"><rect x="3" y="1" width="8" height="12" rx="1.5" fill="none" stroke="#1f6fc1" stroke-width="1.6"/></svg>0427 561 903</li>
    <li><svg viewBox="0 0 14 14"><rect x="1" y="5" width="12" height="7" rx="1" fill="#1f6fc1"/><rect x="4" y="2" width="6" height="4" fill="#1f6fc1"/></svg>6457 2183</li>
    <li><svg viewBox="0 0 14 14"><rect x="1" y="3" width="12" height="9" fill="none" stroke="#1f6fc1" stroke-width="1.6"/><path d="M1 3l6 5 6-5" fill="none" stroke="#1f6fc1" stroke-width="1.6"/></svg>marcus.k.diet@fernmail.com</li>
    <li><svg viewBox="0 0 14 14"><circle cx="7" cy="7" r="6" fill="#1f6fc1"/><path d="M1 7h12M7 1c-3 3-3 9 0 12M7 1c3 3 3 9 0 12" fill="none" stroke="#fff" stroke-width="1"/></svg>www.brightfieldnutrition.com.au</li>
  </ul>

  <div class="locations">
    <div class="location">
      <div class="location__name">Pinebrook Medical Centre</div>
      Cnr Elm &amp; Harper Streets<br>Pinebrook East<br>Corrin 7312<br>pinebrookmedical.com.au
    </div>
    <div class="location">
      <div class="location__name">Hollis Medical</div>
      4/118 Corrin Road<br>Hollis Vale<br>Corrin 7310
    </div>
    <div class="location">
      <div class="location__name">North Corrin Health</div>
      9 Alder Drive<br>Northbank<br>Corrin 7311<br>northcorrinhealth.com.au
    </div>
    <div class="location">
      <div class="location__name">Ashcombe Doctors Surgery</div>
      6 Kestrel Road<br>Ashcombe<br>Corrin<br>ashcombedoctors.com.au
    </div>
  </div>
</section>

</body>
</html>
```